Locksmith Business Cards

My father-in-law is in need of new business cards for his locksmith business and I need to impress him. Kindly help me out!

You can see the previous business card attached. It is a family run business in North Wales.

No individual names on the cards.

Key Things to Feature:
- The words "Prompt", "Local", "Reliable" (as you can see under the logo on the website)
- 24h Emergency Service
- Covering All of North Wales, the Wirral and Chester
- The color blue
- A key or a lock would be interesting (similar to the ones that come up when you google locksmith business card)

Optional (only if design includes bullet points, like the example below):
https://imgvaultcdn.net/samples/208314/55172/55172_3904821_208314_image.jpg
- Residential / Commercial / Automotive
- Alarms & Cameras
- Key Cutting & Safes

https://www.brynhafod-locksmiths.co.uk/

Industry/Entity Type

Locksmith

Contact Information for Business Card

01632 960 418
07700 900 362
brynhafodlocksmiths@mailvane.com
Brynhafod Locksmiths, The Willow Barn, 7 Tannery Rd., Llandudno LL99 4QX
www.brynhafod-locksmiths.co.uk

Requirements
Must have
• - The words "Prompt", "Local", "Reliable" (as you can see under the logo on the website)
• - 24h Emergency Service
• - Covering All of North Wales, the Wirral and Chester
Nice to have
• - A key or a lock would be interesting (similar to the ones that come up when you google locksmith business card)

```html
<!DOCTYPE html>
<html lang="en">
<head>
<meta charset="utf-8">
<title>Brynhafod Locksmiths – Business Cards</title>
<link rel="stylesheet" href="https://fonts.googleapis.com/css2?family=Oswald:wght@400;500&family=Roboto+Condensed:wght@400;500&display=swap">
<style>
  :root {
    --navy: #2b2d78;
    --blue-accent: #4b5eab;
    --white: #ffffff;
    --paper: #e9eaee;
    --text-navy: #2b2d78;
  }
  * { margin: 0; padding: 0; box-sizing: border-box; }
  html, body { width: 1200px; height: 896px; overflow: hidden; }
  body {
    background: var(--paper);
    font-family: "Roboto Condensed", sans-serif;
    position: relative;
  }
  .card {
    position: absolute;
    width: 540px;
    height: 330px;
    border-radius: 22px;
    overflow: hidden;
    box-shadow: 0 6px 18px rgba(0,0,0,0.18);
  }
  .brand {
    position: absolute;
    display: flex;
    align-items: center;
    gap: 14px;
  }
  .brand__mark {
    width: 46px; height: 46px;
    border-radius: 6px;
    flex: none;
  }
  .brand__name {
    font-family: "Oswald", sans-serif;
    font-weight: 500;
    font-size: 34px;
    line-height: 1.0;
    text-transform: uppercase;
    letter-spacing: 0.5px;
  }

  /* Back of card */
  .card--back {
    left: 30px; top: 283px;
    background: var(--navy);
    color: var(--white);
  }
  .card--back .brand { left: 40px; top: 40px; }
  .card--back .brand__mark { background: var(--white); }
  .card--back .brand__name { color: var(--white); }
  .tagline-emergency {
    position: absolute;
    left: 100px; top: 134px;
    font-size: 24px;
  }
  .services {
    position: absolute;
    left: 116px; top: 178px;
    list-style: none;
    font-size: 21px;
    line-height: 25px;
  }
  .services li::before {
    content: "";
    display: inline-block;
    width: 8px; height: 8px;
    border-radius: 50%;
    background: var(--white);
    margin-right: 14px;
    vertical-align: middle;
  }

  /* Front of card */
  .card--front {
    left: 630px; top: 283px;
    background: var(--white);
    color: var(--text-navy);
  }
  .card__swoosh { position: absolute; inset: 0; }
  .card--front .brand { left: 30px; top: 160px; }
  .card--front .brand__mark { background: var(--navy); }
  .card--front .brand__name { color: var(--navy); font-size: 29px; }
  .motto {
    position: absolute;
    left: 30px; top: 232px;
    font-size: 19px;
    color: var(--text-navy);
  }
  .coverage {
    position: absolute;
    left: 30px; top: 264px;
    width: 210px;
    font-size: 13px;
    line-height: 16px;
    color: var(--text-navy);
  }
  .contact {
    position: absolute;
    right: 26px; top: 112px;
    width: 250px;
    text-align: right;
    color: var(--white);
    font-size: 13.5px;
    line-height: 17px;
  }
  .contact__address { margin-bottom: 14px; }
  .contact__group { margin-bottom: 12px; }
  .contact__line { display: flex; justify-content: flex-end; align-items: center; gap: 6px; }
  .contact__icon { width: 10px; height: 10px; flex: none; }
</style>
</head>
<body>

<section class="card card--back" aria-label="Card back">
  <div class="brand">
    <span class="brand__mark"></span>
    <span class="brand__name">Brynhafod<br>Locksmiths</span>
  </div>
  <p class="tagline-emergency">24h Emergency Service</p>
  <ul class="services">
    <li>Residential</li>
    <li>Commercial</li>
    <li>Automotive</li>
    <li>Alarms &amp; Cameras</li>
    <li>Key Cutting &amp; Safes</li>
  </ul>
</section>

<section class="card card--front" aria-label="Card front">
  <svg class="card__swoosh" viewBox="0 0 540 330" preserveAspectRatio="none" aria-hidden="true">
    <path d="M250 330 C250 200 320 110 540 60 L540 330 Z" fill="#4b5eab"/>
    <path d="M270 330 C268 205 340 125 540 84 L540 330 Z" fill="#2b2d78"/>
  </svg>

  <div class="contact">
    <p class="contact__address">Brynhafod Locksmiths,<br>The Willow Barn, 7 Tannery Rd.,<br>Llandudno LL99 4QX</p>
    <div class="contact__group">
      <p class="contact__line">01632 960 418
        <svg class="contact__icon" viewBox="0 0 10 10" aria-hidden="true"><path d="M2 1 L4 3 L3 4.2 C3.8 5.6 4.6 6.4 5.8 7 L7 6 L9 8 L7.6 9.4 C4 8.6 1.4 6 0.6 2.4 Z" fill="#fff"/></svg>
      </p>
      <p class="contact__line">07700 900 362
        <svg class="contact__icon" viewBox="0 0 10 10" aria-hidden="true"><rect x="2.5" y="0.5" width="5" height="9" rx="1" fill="none" stroke="#fff"/></svg>
      </p>
    </div>
    <p class="contact__line">brynhafodlocksmiths@mailvane.com
      <svg class="contact__icon" viewBox="0 0 10 10" aria-hidden="true"><rect x="0.5" y="2" width="9" height="6.5" fill="none" stroke="#fff"/><path d="M0.5 2 L5 5.6 L9.5 2" fill="none" stroke="#fff"/></svg>
    </p>
    <p class="contact__line">www.brynhafod-locksmiths.co.uk
      <svg class="contact__icon" viewBox="0 0 10 10" aria-hidden="true"><circle cx="5" cy="5" r="4.5" fill="none" stroke="#fff"/><path d="M0.5 5 H9.5 M5 0.5 C2.5 3 2.5 7 5 9.5 M5 0.5 C7.5 3 7.5 7 5 9.5" fill="none" stroke="#fff" stroke-width="0.8"/></svg>
    </p>
  </div>

  <div class="brand">
    <span class="brand__mark"></span>
    <span class="brand__name">Brynhafod<br>Locksmiths</span>
  </div>
  <p class="motto">Prompt. Local. Reliable</p>
  <p class="coverage">Covering All of North Wales,<br>the Wirral and Chester</p>
</section>

</body>
</html>
```